TA BRAMLEY BUSINESS CARD DESIGN PROJECT

We need to utilize our logo that was expertly created on PixelHarbor and now need to match this with a business card design.

```html
<!DOCTYPE html>
<html lang="en">
<head>
<meta charset="utf-8">
<title>TA Bramley Business Card</title>
<link href="https://fonts.googleapis.com/css2?family=Montserrat:wght@400;500;700&display=swap" rel="stylesheet">
<style>
  :root {
    --brand-blue: #0c58b0;
    --card-black: #141414;
    --stripe-black: #0d1a2b;
    --paper: #ffffff;
    --backdrop: #d9d9d9;
    --ink-light: #ffffff;
  }
  * { margin: 0; padding: 0; box-sizing: border-box; }
  html, body {
    width: 1200px; height: 900px; overflow: hidden;
    background: var(--backdrop);
    font-family: "Montserrat", sans-serif;
  }
  .canvas { position: relative; width: 1200px; height: 900px; }
  .card {
    position: absolute; width: 600px; height: 343px;
    border-radius: 22px; overflow: hidden;
    box-shadow: 0 10px 28px rgba(0,0,0,0.25);
  }
  .card-front { left: 80px; top: 70px; background: var(--paper); }
  .card-back { left: 520px; top: 480px; background: var(--brand-blue); }

  .front-mark {
    position: absolute; inset: 0;
    display: flex; align-items: center; justify-content: center; gap: 18px;
  }
  .mark-dot {
    width: 46px; height: 46px; border-radius: 50%;
    background: var(--brand-blue);
  }
  .front-name {
    color: var(--brand-blue); font-weight: 700; font-size: 52px;
    letter-spacing: 4px;
  }

  .back-shape { position: absolute; inset: 0; width: 600px; height: 343px; }
  .back-mark {
    position: absolute; right: 34px; top: 42px;
    color: var(--ink-light); font-weight: 700; font-size: 30px; letter-spacing: 3px;
  }
  .person { position: absolute; left: 36px; top: 204px; }
  .person-name {
    color: var(--brand-blue); font-weight: 700; font-size: 20px;
    letter-spacing: 0.5px; line-height: 1.1;
  }
  .person-title { color: var(--ink-light); font-size: 15px; margin-top: 2px; }
  .rule {
    position: absolute; left: 250px; right: 28px; top: 222px;
    height: 1px; background: var(--brand-blue);
  }
  .contact-list {
    position: absolute; left: 36px; top: 268px; list-style: none;
    color: var(--ink-light); font-size: 13px;
  }
  .contact-list li { display: flex; align-items: center; gap: 9px; height: 21px; }
  .contact-list svg { width: 13px; height: 13px; fill: var(--brand-blue); }
  .address {
    position: absolute; right: 32px; top: 238px; text-align: right;
    color: var(--ink-light); font-size: 14px; line-height: 1.45;
  }
</style>
</head>
<body>
<main class="canvas">

  <section class="card card-front" aria-label="Business card front">
    <div class="front-mark">
      <span class="mark-dot"></span>
      <span class="front-name">TA BRAMLEY</span>
    </div>
  </section>

  <section class="card card-back" aria-label="Business card back">
    <svg class="back-shape" viewBox="0 0 600 343" aria-hidden="true">
      <path d="M0,215 C160,150 380,125 600,45 L600,343 L0,343 Z" fill="var(--card-black)"/>
      <path d="M22,205 C170,140 390,118 580,55" fill="none" stroke="var(--stripe-black)" stroke-width="4"/>
    </svg>

    <div class="back-mark">TA BRAMLEY</div>

    <div class="person">
      <p class="person-name">DANA WHITFIELD</p>
      <p class="person-title">Managing Director</p>
    </div>
    <div class="rule"></div>

    <ul class="contact-list">
      <li>
        <svg viewBox="0 0 24 24"><path d="M6.6 10.8a15.1 15.1 0 0 0 6.6 6.6l2.2-2.2a1 1 0 0 1 1-.25 11.4 11.4 0 0 0 3.6.57 1 1 0 0 1 1 1V20a1 1 0 0 1-1 1A17 17 0 0 1 3 4a1 1 0 0 1 1-1h3.5a1 1 0 0 1 1 1c0 1.25.2 2.45.57 3.57a1 1 0 0 1-.25 1z"/></svg>
        555 210 4477
      </li>
      <li>
        <svg viewBox="0 0 24 24"><path d="M2 5h20v14H2z M2 5l10 8 10-8" /></svg>
        hello@tabramley.com
      </li>
      <li>
        <svg viewBox="0 0 24 24"><circle cx="12" cy="12" r="10"/></svg>
        www.tabramley.com
      </li>
    </ul>

    <address class="address" style="font-style:normal">
      418 Larkspur Lane NW<br>
      Maple Ridge, GA 30877
    </address>
  </section>

</main>
</body>
</html>
```